2018 Desk Calendar Design with Better Spine, Better Health with Chiropractic

In conjunction with the Federation of Spinal Wellness Malaysia (FSW), we are organizing a 2018 desk calendar design. The cover page and monthly design size is 210mm (H) x 195mm (W). The will be a total of 27 designs including a cover page (front) [Sample 1], cover page (back) Malaysia National & States Holiday 2018 (https://restdaylist.example.my/2018-dates/) [Sample 2], 12 months design (front) [Sample 3 and 4], 12 months design (back) [Sample 5], Last page (2017 and 2019 calendar) [Sample 6].

Below are some recommendations for monthly back cover design. The main theme remain as Better SPINE, Better HEALTH with CHIROPRACTIC. Each month can in collaborate with of the following element:-

Suggestion 1 (Celebration of the Month)
January - New Year
February - Chinese New Year
March -
April -
May - Labour Day
June - Aidilfitri Festival
July-
August - Independent Day
September - Malaysia Day
October - World Spine Day
November - Deepavali Festival
December - Christmas

Suggestion 2 (States in Malaysia)
January - Perlis
February - Kedah
March - Penang
April - Perak
May - Selangor
June - Negeri Sembilan
July- Melaka
August - Johor
September - Pahang
October - Terengganu
November - Kelantan
December - Sabah & Sarawak

Target Market(s)

Chiropractors and Public

Industry/Entity Type

Chiropractor

Colors

Designer to choose colors to be used in the design.

Requirements
Must have
• The theme for the desk calendar design is Better Spine, Better Health with Chiropractic.
• The cover page should include 5th Anniversary element.
Nice to have
• Lunar or Islamic calendar is optional in the Gregorian calendar.
• AI Format
• Footnote of each page www.spinefsw.example.org

```html
<!DOCTYPE html>
<html lang="en">
<head>
<meta charset="utf-8">
<title>FSW Desk Calendar – 2017 and 2019</title>
<link href="https://fonts.googleapis.com/css2?family=Krona+One&family=Arimo:wght@400;700&display=swap" rel="stylesheet">
<style>
:root{
  --paper:#ffffff;
  --ink:#141414;
  --sunday:#e3161e;
  --navy:#2b3990;
  --lime:#d3d92b;
  --lime-light:#eef0b0;
  --olive:#b5b04e;
}
html,body{margin:0;padding:0;overflow:hidden;background:var(--paper)}
.page{position:relative;width:1117px;height:1200px;overflow:hidden;background:var(--paper);color:var(--ink);font-family:"Krona One",sans-serif}
.year-title{position:absolute;margin:0;font-size:20px;letter-spacing:3px;font-weight:400}
.year-2017{left:252px;top:62px}
.year-2019{left:800px;top:56px}
.month{position:absolute;width:227px}
.month h3{margin:0 0 4px;height:16px;text-align:center;font-size:12px;font-weight:400;font-variant:small-caps;letter-spacing:1.5px;text-transform:lowercase}
.days{display:flex}
.days span{display:block;width:32.4px;font-size:10px;line-height:21.6px;white-space:nowrap}
.days span:last-child{color:var(--sunday)}
.c1{left:68px}.c2{left:308px}.c3{left:607px}.c4{left:861px}
.r1{top:112px}.r2{top:270px}.r3{top:419px}.r4{top:576px}.r5{top:732px}.r6{top:894px}
.brand{position:absolute;left:30px;top:1050px;width:130px;height:140px;display:flex;flex-direction:column;align-items:center;justify-content:center;gap:8px}
.brand-dot{width:64px;height:64px;border-radius:50%;background:var(--navy)}
.brand-name{font-family:"Krona One",sans-serif;font-size:22px;color:var(--navy)}
.anniversary-mark{position:absolute;left:160px;top:1056px;width:158px;height:130px;border-radius:12px;background:linear-gradient(135deg,#dfe3f4,#fbf2c8)}
.accent-band{position:absolute;left:340px;top:1070px;width:777px;height:130px;background:linear-gradient(160deg,rgba(255,255,255,0) 0%,var(--lime-light) 35%,var(--lime) 70%,var(--olive) 100%)}
.site-url{position:absolute;right:18px;top:1162px;font-family:"Arimo",sans-serif;font-size:20px;color:var(--ink)}
</style>
</head>
<body>
<div class="page">
  <h2 class="year-title year-2017">2017</h2>
  <h2 class="year-title year-2019">2019</h2>

  <!-- 2017 first half -->
  <section class="month c1 r1"><h3>January</h3><div class="days">
    <span>M<br>30<br>2<br>9<br>16<br>23</span><span>T<br>31<br>3<br>10<br>17<br>24</span><span>W<br><br>4<br>11<br>18<br>25</span><span>T<br><br>5<br>12<br>19<br>26</span><span>F<br><br>6<br>13<br>20<br>27</span><span>S<br><br>7<br>14<br>21<br>28</span><span>S<br>1<br>8<br>15<br>22<br>29</span>
  </div></section>
  <section class="month c1 r2"><h3>February</h3><div class="days">
    <span>M<br><br>6<br>13<br>20<br>27</span><span>T<br><br>7<br>14<br>21<br>28</span><span>W<br>1<br>8<br>15<br>22</span><span>T<br>2<br>9<br>16<br>23</span><span>F<br>3<br>10<br>17<br>24</span><span>S<br>4<br>11<br>18<br>25</span><span>S<br>5<br>12<br>19<br>26</span>
  </div></section>
  <section class="month c1 r3"><h3>March</h3><div class="days">
    <span>M<br><br>6<br>13<br>20<br>27</span><span>T<br><br>7<br>14<br>21<br>28</span><span>W<br>1<br>8<br>15<br>22<br>29</span><span>T<br>2<br>9<br>16<br>23<br>30</span><span>F<br>3<br>10<br>17<br>24<br>31</span><span>S<br>4<br>11<br>18<br>25</span><span>S<br>5<br>12<br>19<br>26</span>
  </div></section>
  <section class="month c1 r4"><h3>April</h3><div class="days">
    <span>M<br><br>3<br>10<br>17<br>24</span><span>T<br><br>4<br>11<br>18<br>25</span><span>W<br><br>5<br>12<br>19<br>26</span><span>T<br><br>6<br>13<br>20<br>27</span><span>F<br><br>7<br>14<br>21<br>28</span><span>S<br>1<br>8<br>15<br>22<br>29</span><span>S<br>2<br>9<br>16<br>23<br>30</span>
  </div></section>
  <section class="month c1 r5"><h3>May</h3><div class="days">
    <span>M<br>1<br>8<br>15<br>22<br>29</span><span>T<br>2<br>9<br>16<br>23<br>30</span><span>W<br>3<br>10<br>17<br>24<br>31</span><span>T<br>4<br>11<br>18<br>25</span><span>F<br>5<br>12<br>19<br>26</span><span>S<br>6<br>13<br>20<br>27</span><span>S<br>7<br>14<br>21<br>28</span>
  </div></section>
  <section class="month c1 r6"><h3>June</h3><div class="days">
    <span>M<br><br>5<br>12<br>19<br>26</span><span>T<br><br>6<br>13<br>20<br>27</span><span>W<br><br>7<br>14<br>21<br>28</span><span>T<br>1<br>8<br>15<br>22<br>29</span><span>F<br>2<br>9<br>16<br>23<br>30</span><span>S<br>3<br>10<br>17<br>24</span><span>S<br>4<br>11<br>18<br>25</span>
  </div></section>

  <!-- 2017 second half -->
  <section class="month c2 r1"><h3>July</h3><div class="days">
    <span>M<br>31<br>3<br>10<br>17<br>24</span><span>T<br><br>4<br>11<br>18<br>25</span><span>W<br><br>5<br>12<br>19<br>26</span><span>T<br><br>6<br>13<br>20<br>27</span><span>F<br><br>7<br>14<br>21<br>28</span><span>S<br>1<br>8<br>15<br>22<br>29</span><span>S<br>2<br>9<br>16<br>23<br>30</span>
  </div></section>
  <section class="month c2 r2"><h3>August</h3><div class="days">
    <span>M<br><br>7<br>14<br>21<br>28</span><span>T<br>1<br>8<br>15<br>22<br>29</span><span>W<br>2<br>9<br>16<br>23<br>30</span><span>T<br>3<br>10<br>17<br>24<br>31</span><span>F<br>4<br>11<br>18<br>25</span><span>S<br>5<br>12<br>19<br>26</span><span>S<br>6<br>13<br>20<br>27</span>
  </div></section>
  <section class="month c2 r3"><h3>September</h3><div class="days">
    <span>M<br><br>4<br>11<br>18<br>25</span><span>T<br><br>5<br>12<br>19<br>26</span><span>W<br><br>6<br>13<br>20<br>27</span><span>T<br><br>7<br>14<br>21<br>28</span><span>F<br>1<br>8<br>15<br>22<br>29</span><span>S<br>2<br>9<br>16<br>23<br>30</span><span>S<br>3<br>10<br>17<br>24</span>
  </div></section>
  <section class="month c2 r4"><h3>October</h3><div class="days">
    <span>M<br>30<br>2<br>9<br>16<br>23</span><span>T<br>31<br>3<br>10<br>17<br>24</span><span>W<br><br>4<br>11<br>18<br>25</span><span>T<br><br>5<br>12<br>19<br>26</span><span>F<br><br>6<br>13<br>20<br>27</span><span>S<br><br>7<br>14<br>21<br>28</span><span>S<br>1<br>8<br>15<br>22<br>29</span>
  </div></section>
  <section class="month c2 r5"><h3>November</h3><div class="days">
    <span>M<br><br>6<br>13<br>20<br>27</span><span>T<br><br>7<br>14<br>21<br>28</span><span>W<br>1<br>8<br>15<br>22<br>29</span><span>T<br>2<br>9<br>16<br>23<br>30</span><span>F<br>3<br>10<br>17<br>24</span><span>S<br>4<br>11<br>18<br>25</span><span>S<br>5<br>12<br>19<br>26</span>
  </div></section>
  <section class="month c2 r6"><h3>December</h3><div class="days">
    <span>M<br><br>4<br>11<br>18<br>25</span><span>T<br><br>5<br>12<br>19<br>26</span><span>W<br><br>6<br>13<br>20<br>27</span><span>T<br><br>7<br>14<br>21<br>28</span><span>F<br>1<br>8<br>15<br>22<br>29</span><span>S<br>2<br>9<br>16<br>23<br>30</span><span>S<br>3<br>10<br>17<br>24<br>31</span>
  </div></section>

  <!-- 2019 first half -->
  <section class="month c3 r1"><h3>January</h3><div class="days">
    <span>M<br><br>7<br>14<br>21<br>28</span><span>T<br>1<br>8<br>15<br>22<br>29</span><span>W<br>2<br>9<br>16<br>23<br>30</span><span>T<br>3<br>10<br>17<br>24<br>31</span><span>F<br>4<br>11<br>18<br>25</span><span>S<br>5<br>12<br>19<br>26</span><span>S<br>6<br>13<br>20<br>27</span>
  </div></section>
  <section class="month c3 r2"><h3>February</h3><div class="days">
    <span>M<br><br>4<br>11<br>18<br>25</span><span>T<br><br>5<br>12<br>19<br>26</span><span>W<br><br>6<br>13<br>20<br>27</span><span>T<br><br>7<br>14<br>21<br>28</span><span>F<br>1<br>8<br>15<br>22</span><span>S<br>2<br>9<br>16<br>23</span><span>S<br>3<br>10<br>17<br>24</span>
  </div></section>
  <section class="month c3 r3"><h3>March</h3><div class="days">
    <span>M<br><br>4<br>11<br>18<br>25</span><span>T<br><br>5<br>12<br>19<br>26</span><span>W<br><br>6<br>13<br>20<br>27</span><span>T<br><br>7<br>14<br>21<br>28</span><span>F<br>1<br>8<br>15<br>22<br>29</span><span>S<br>2<br>9<br>16<br>23<br>30</span><span>S<br>3<br>10<br>17<br>24<br>31</span>
  </div></section>
  <section class="month c3 r4"><h3>April</h3><div class="days">
    <span>M<br>1<br>8<br>15<br>22<br>29</span><span>T<br>2<br>9<br>16<br>23<br>30</span><span>W<br>3<br>10<br>17<br>24</span><span>T<br>4<br>11<br>18<br>25</span><span>F<br>5<br>12<br>19<br>26</span><span>S<br>6<br>13<br>20<br>27</span><span>S<br>7<br>14<br>21<br>28</span>
  </div></section>
  <section class="month c3 r5"><h3>May</h3><div class="days">
    <span>M<br><br>6<br>13<br>20<br>27</span><span>T<br><br>7<br>14<br>21<br>28</span><span>W<br>1<br>8<br>15<br>22<br>29</span><span>T<br>2<br>9<br>16<br>23<br>30</span><span>F<br>3<br>10<br>17<br>24<br>31</span><span>S<br>4<br>11<br>18<br>25</span><span>S<br>5<br>12<br>19<br>26</span>
  </div></section>
  <section class="month c3 r6"><h3>June</h3><div class="days">
    <span>M<br><br>3<br>10<br>17<br>24</span><span>T<br><br>4<br>11<br>18<br>25</span><span>W<br><br>5<br>12<br>19<br>26</span><span>T<br><br>6<br>13<br>20<br>27</span><span>F<br><br>7<br>14<br>21<br>28</span><span>S<br>1<br>8<br>15<br>22<br>29</span><span>S<br>2<br>9<br>16<br>23<br>30</span>
  </div></section>

  <!-- 2019 second half -->
  <section class="month c4 r1"><h3>July</h3><div class="days">
    <span>M<br>1<br>8<br>15<br>22<br>29</span><span>T<br>2<br>9<br>16<br>23<br>30</span><span>W<br>3<br>10<br>17<br>24<br>31</span><span>T<br>4<br>11<br>18<br>25</span><span>F<br>5<br>12<br>19<br>26</span><span>S<br>6<br>13<br>20<br>27</span><span>S<br>7<br>14<br>21<br>28</span>
  </div></section>
  <section class="month c4 r2"><h3>August</h3><div class="days">
    <span>M<br><br>5<br>12<br>19<br>26</span><span>T<br><br>6<br>13<br>20<br>27</span><span>W<br><br>7<br>14<br>21<br>28</span><span>T<br>1<br>8<br>15<br>22<br>29</span><span>F<br>2<br>9<br>16<br>23<br>30</span><span>S<br>3<br>10<br>17<br>24<br>31</span><span>S<br>4<br>11<br>18<br>25</span>
  </div></section>
  <section class="month c4 r3"><h3>September</h3><div class="days">
    <span>M<br>30<br>2<br>9<br>16<br>23</span><span>T<br><br>3<br>10<br>17<br>24</span><span>W<br><br>4<br>11<br>18<br>25</span><span>T<br><br>5<br>12<br>19<br>26</span><span>F<br><br>6<br>13<br>20<br>27</span><span>S<br><br>7<br>14<br>21<br>28</span><span>S<br>1<br>8<br>15<br>22<br>29</span>
  </div></section>
  <section class="month c4 r4"><h3>October</h3><div class="days">
    <span>M<br><br>7<br>14<br>21<br>28</span><span>T<br>1<br>8<br>15<br>22<br>29</span><span>W<br>2<br>9<br>16<br>23<br>30</span><span>T<br>3<br>10<br>17<br>24<br>31</span><span>F<br>4<br>11<br>18<br>25</span><span>S<br>5<br>12<br>19<br>26</span><span>S<br>6<br>13<br>20<br>27</span>
  </div></section>
  <section class="month c4 r5"><h3>November</h3><div class="days">
    <span>M<br><br>4<br>11<br>18<br>25</span><span>T<br><br>5<br>12<br>19<br>26</span><span>W<br><br>6<br>13<br>20<br>27</span><span>T<br><br>7<br>14<br>21<br>28</span><span>F<br>1<br>8<br>15<br>22<br>29</span><span>S<br>2<br>9<br>16<br>23<br>30</span><span>S<br>3<br>10<br>17<br>24</span>
  </div></section>
  <section class="month c4 r6"><h3>December</h3><div class="days">
    <span>M<br>30<br>2<br>9<br>16<br>23</span><span>T<br>31<br>3<br>10<br>17<br>24</span><span>W<br><br>4<br>11<br>18<br>25</span><span>T<br><br>5<br>12<br>19<br>26</span><span>F<br><br>6<br>13<br>20<br>27</span><span>S<br><br>7<br>14<br>21<br>28</span><span>S<br>1<br>8<br>15<br>22<br>29</span>
  </div></section>

  <div class="accent-band" role="img" aria-label="Decorative lime and olive accent area"></div>

  <div class="brand">
    <span class="brand-dot"></span>
    <span class="brand-name">FSW</span>
  </div>
  <div class="anniversary-mark" role="img" aria-label="Fifth anniversary emblem"></div>

  <div class="site-url">www.spinefsw.example.org</div>
</div>
</body>
</html>
```